Corvane Freight Company Business Card Design

We are a company that delivers natural saltwater (from the ocean) to aquarium companies, restaurants and home marine tanks. I would like a new business card to suit.

Must include Name, company name, abn, contact number and website as well as logo (see attached).

Looking for a design that stands out, has a clean but unique appearance.

Double and single sided entries welcome

Business

• Logo

```html
<!DOCTYPE html>
<html lang="en">
<head>
<meta charset="utf-8">
<title>Corvane Freight Company – Business Card</title>
<link rel="stylesheet" href="https://fonts.googleapis.com/css2?family=Source+Sans+3:ital,wght@0,400;0,600;0,700;1,700&display=swap">
<style>
  :root {
    --backdrop: #161616;
    --brand-blue: #0a5fad;
    --sky-blue: #1d9ad8;
    --light-blue: #5cc8f2;
    --ink: #3a3a3a;
    --card-white: #ffffff;
    --rule-dark: #1f1f1f;
  }
  * { box-sizing: border-box; margin: 0; padding: 0; }
  html, body {
    width: 1200px; height: 420px; overflow: hidden;
    background: var(--backdrop);
    font-family: "Source Sans 3", "Myriad Pro", Arial, sans-serif;
  }
  .stage { position: relative; width: 1200px; height: 420px; }
  .card {
    position: absolute; top: 66px; width: 518px; height: 294px;
    border-radius: 26px; overflow: hidden;
  }
  .card--front { left: 69px; background: var(--card-white); }
  .card--back {
    left: 620px; background: var(--brand-blue);
    border: 1.5px solid #c9d3de;
    display: flex; align-items: center; justify-content: center;
  }

  .front-brand {
    position: absolute; left: 40px; top: 95px; width: 250px;
    color: var(--sky-blue); font-size: 31px; font-weight: 400; line-height: 1.05;
  }
  .front-divider {
    position: absolute; left: 314px; top: 54px; width: 2px; height: 118px;
    background: linear-gradient(to bottom, rgba(0,0,0,0), #9a9a9a 20%, #9a9a9a 80%, rgba(0,0,0,0));
  }
  .contact { position: absolute; left: 340px; top: 66px; color: var(--ink); }
  .contact__name { color: var(--brand-blue); font-size: 19px; font-weight: 700; line-height: 1.1; }
  .contact__title { font-size: 14px; margin-top: 3px; }
  .contact__list { list-style: none; margin-top: 16px; font-size: 13.5px; color: var(--brand-blue); }
  .contact__list li { display: flex; align-items: center; gap: 7px; height: 19px; }
  .contact__list svg { width: 11px; height: 11px; fill: var(--ink); }

  .front-wave { position: absolute; left: 0; bottom: 0; width: 518px; height: 294px; }
  .address {
    position: absolute; left: 33px; top: 236px;
    color: var(--card-white); font-size: 12.5px; line-height: 18px;
  }

  .back-brand {
    color: var(--card-white); font-size: 54px; font-weight: 400;
    line-height: 1.0; text-align: center;
  }
</style>
</head>
<body>
<main class="stage">
  <section class="card card--front" aria-label="Business card front">
    <svg class="front-wave" viewBox="0 0 518 294" aria-hidden="true">
      <path d="M0,214 C120,188 220,190 330,222 C410,246 468,262 518,258 L518,294 L0,294 Z" fill="var(--brand-blue)"/>
      <path d="M0,208 C120,182 222,186 332,218 C410,242 470,258 518,252" fill="none" stroke="var(--rule-dark)" stroke-width="2.2"/>
      <path d="M0,205 C120,178 224,182 334,214" fill="none" stroke="#ffffff" stroke-width="1.5"/>
      <path d="M268,212 C360,236 450,256 518,248 L518,258 C446,268 362,252 268,212 Z" fill="var(--light-blue)"/>
    </svg>

    <div class="front-brand">Corvane Freight Company</div>
    <div class="front-divider"></div>

    <div class="contact">
      <p class="contact__name">Your Name</p>
      <p class="contact__title">Title</p>
      <ul class="contact__list">
        <li>
          <svg viewBox="0 0 24 24" aria-hidden="true"><path d="M6.6 10.8a15.1 15.1 0 0 0 6.6 6.6l2.2-2.2a1 1 0 0 1 1-.25 11.4 11.4 0 0 0 3.6.57 1 1 0 0 1 1 1V20a1 1 0 0 1-1 1A17 17 0 0 1 3 4a1 1 0 0 1 1-1h3.5a1 1 0 0 1 1 1c0 1.25.2 2.45.57 3.57a1 1 0 0 1-.25 1z"/></svg>
          <span>123-456-7892</span>
        </li>
        <li>
          <svg viewBox="0 0 24 24" aria-hidden="true"><path d="M12 2a10 10 0 1 0 0 20 10 10 0 0 0 0-20zm6.9 6h-2.9a15.6 15.6 0 0 0-1.4-3.6A8 8 0 0 1 18.9 8zM12 4a14 14 0 0 1 1.9 4h-3.8A14 14 0 0 1 12 4zM4.3 14a8 8 0 0 1 0-4h3.4a16 16 0 0 0 0 4zm.8 2h2.9a15.6 15.6 0 0 0 1.4 3.6A8 8 0 0 1 5.1 16zM8 8H5.1a8 8 0 0 1 4.3-3.6A15.6 15.6 0 0 0 8 8zm4 12a14 14 0 0 1-1.9-4h3.8A14 14 0 0 1 12 20zm2.3-6H9.7a14.7 14.7 0 0 1 0-4h4.6a14.7 14.7 0 0 1 0 4zm.3 5.6a15.6 15.6 0 0 0 1.4-3.6h2.9a8 8 0 0 1-4.3 3.6zM16.3 14a16 16 0 0 0 0-4h3.4a8 8 0 0 1 0 4z"/></svg>
          <span>www.corvanefreight.com</span>
        </li>
      </ul>
    </div>

    <address class="address" style="font-style:normal">
      Street Name, City Name<br>
      State, Zip Code<br>
      ABN: 123456789
    </address>
  </section>

  <section class="card card--back" aria-label="Business card back">
    <div class="back-brand">Corvane Freight<br>Company</div>
  </section>
</main>
</body>
</html>
```